Brintel Works - Fast, Efficient and Gas Mainteance for Domestic, Commercial and Industrial clients

We are in the process of purchasing a new business and would like to get a new logo and business card.
Business is a gas maintenance business that also does new gas installations.
Has been established since 1988.
Services include:
Install all types of gas appliances & equipment inc. hot water units
Maintain / repair / replace all types of gas appliances & equipment

Target Market(s)

Domestic, Commercial and Industrial clients

Industry/Entity Type

Business

Contact Information for Business Card

admin@brintelworks.com.au
07 3918 4726
Brintel Works PTY LTD

Logo Text

Gas Fitting & Plumbing Maintenance Specialists

Font styles to use
Sans Serif

Requirements
Must have
• Logo
• Business name, contact number, email address, web address
• Domestic | Commercial | Industrial Est Since 1988
Nice to have
• Possibly a black card with a flame logo to one side
Should not have
• Spelling errors

```html
<!DOCTYPE html>
<html lang="en">
<head>
<meta charset="utf-8">
<title>Brintel Works PTY LTD – Business Card</title>
<link rel="stylesheet" href="https://fonts.googleapis.com/css2?family=Tinos:wght@400;700&family=Open+Sans:wght@400;600&family=Arimo:wght@400&family=Pinyon+Script&display=swap">
<style>
  :root {
    --page: #e6e6e6;
    --card-light: #ececec;
    --card-dark: #130c0d;
    --card-black: #000000;
    --brand-red: #e8533a;
    --text-grey: #4a4a4a;
    --text-mid: #5e5e5e;
    --text-white: #ffffff;
    --tag-grey: #d6d6d6;
  }
  * { margin: 0; padding: 0; box-sizing: border-box; }
  html, body {
    width: 1189px; height: 1200px; overflow: hidden;
    background: var(--page);
  }
  .card {
    position: absolute; left: 140px; width: 918px; height: 524px;
    overflow: hidden; box-shadow: 0 4px 10px rgba(0,0,0,0.25);
  }
  .card--front { top: 45px; background: var(--card-dark); }
  .card--back { top: 624px; background: var(--card-black); }

  .front-header {
    position: absolute; left: 0; top: 0; width: 100%; height: 249px;
    background: var(--card-light);
  }
  .front-rule {
    position: absolute; left: 0; top: 249px; width: 100%; height: 7px;
    background: var(--brand-red);
  }
  .brand-mark {
    position: absolute; left: 16px; top: 40px; width: 96px; height: 96px;
    border-radius: 50%; background: #d8d8d8;
  }
  .brand-name {
    position: absolute; left: 127px; top: 36px;
    font-family: "Tinos", "Times New Roman", serif; font-weight: 700;
    font-size: 68px; line-height: 1; color: var(--brand-red);
    white-space: nowrap; letter-spacing: -0.5px;
  }
  .brand-name .legal {
    font-family: "Open Sans", Arial, sans-serif; font-weight: 600;
    font-size: 16px; color: var(--text-grey); margin-left: 14px; letter-spacing: 0;
  }
  .tagline {
    position: absolute; left: 128px; top: 112px;
    font-family: "Open Sans", Arial, sans-serif; font-weight: 600;
    font-size: 35px; color: var(--text-grey); white-space: nowrap;
  }
  .sectors {
    position: absolute; left: 128px; top: 170px;
    font-family: "Open Sans", Arial, sans-serif; font-weight: 400;
    font-size: 20px; color: var(--text-mid); white-space: nowrap;
    display: flex; align-items: baseline; gap: 22px;
  }
  .sectors .est {
    font-family: "Pinyon Script", cursive; font-size: 30px; color: #777;
  }

  .contact-list {
    position: absolute; left: 72px; top: 306px; list-style: none;
    font-family: "Arimo", Arial, sans-serif; font-size: 27px;
    color: var(--text-white);
  }
  .contact-list li {
    display: flex; align-items: center; height: 39.5px;
  }
  .contact-list svg { width: 18px; height: 18px; margin-right: 11px; flex: none; }

  .appliance-photo {
    position: absolute; left: 545px; top: 256px; width: 373px; height: 268px;
    background: linear-gradient(90deg, rgba(19,12,13,0) 0%, #4a4b4d 12%, #5b5c5f 45%, #8e8f92 70%, #b7b8bb 100%);
  }

  .back-name {
    position: absolute; left: 49px; top: 247px;
    font-family: "Tinos", "Times New Roman", serif; font-weight: 400;
    font-size: 70px; line-height: 1; color: var(--brand-red); white-space: nowrap;
  }
  .back-name .legal { font-size: 40px; color: var(--tag-grey); margin-left: 14px; }
</style>
</head>
<body>
  <section class="card card--front">
    <div class="front-header">
      <div class="brand-mark"></div>
      <h1 class="brand-name">BRINTEL WORKS<span class="legal">PTY LTD</span></h1>
      <p class="tagline">Gas fitting &amp; Plumbing Specialists</p>
      <p class="sectors"><span>Domestic | Commercial | Industrial</span><span class="est">Est Since 1988</span></p>
    </div>
    <div class="front-rule"></div>
    <ul class="contact-list">
      <li>
        <svg viewBox="0 0 18 18"><rect width="18" height="18" fill="var(--brand-red)"/><path d="M5 4h3l1 3-2 1c1 2 2 3 3 3l1-2 3 1v3c-6 1-10-4-9-9z" fill="#fff"/></svg>
        07 3918 4726
      </li>
      <li>
        <svg viewBox="0 0 18 18"><rect width="18" height="18" fill="var(--brand-red)"/><rect x="6" y="3" width="6" height="12" rx="1" fill="#fff"/><rect x="7" y="5" width="4" height="7" fill="var(--brand-red)"/></svg>
        04 2583 9071
      </li>
      <li>
        <svg viewBox="0 0 18 18"><rect width="18" height="18" fill="var(--brand-red)"/><rect x="3" y="5" width="12" height="8" fill="#fff"/><path d="M3 5l6 5 6-5" stroke="var(--brand-red)" stroke-width="1.2" fill="none"/></svg>
        admin@brintelworks.com.au
      </li>
      <li>
        <svg viewBox="0 0 18 18"><rect width="18" height="18" fill="var(--brand-red)"/><circle cx="9" cy="9" r="5.5" fill="none" stroke="#fff" stroke-width="1.5"/><path d="M3.5 9h11M9 3.5c-3 3-3 8 0 11M9 3.5c3 3 3 8 0 11" stroke="#fff" stroke-width="1" fill="none"/></svg>
        www.brintelworks.com.au
      </li>
    </ul>
    <div class="appliance-photo" role="img" aria-label="Photo of a gas log heater with flames beside two hot water units"></div>
  </section>

  <section class="card card--back">
    <h2 class="back-name">BRINTEL WORKS<span class="legal">PTY LTD</span></h2>
  </section>
</body>
</html>
```